Executive Coaching and Spiritual Development Company needs a business card design.

We need a business card design for our company. We already have a logo that was created through Brightloom that we will submit and would like to see this work on black, blue and white backgrounds. Our personal information should be included as well. The design should communicate trust, spirituality, support and partnership.

Industry/Entity Type

Business

Colors
0255a3
33a6d7
ffffff
000000
474747

Requirements
Nice to have
• The colors offered here are just ideas--we are open to other suggestions, too.

```html
<!DOCTYPE html>
<html lang="en">
<head>
<meta charset="utf-8">
<title>Innerway – Business Card</title>
<link rel="stylesheet" href="https://fonts.googleapis.com/css2?family=Lato:wght@400;700;900&display=swap">
<style>
  :root {
    --backdrop: #2a2a2a;
    --card-blue: #34a8db;
    --card-white: #f7f7f7;
    --ink-dark: #0d2531;
    --ink-black: #111111;
    --accent-blue: #2a8fc4;
    --icon-teal: #1f4f5a;
  }
  * { margin: 0; padding: 0; box-sizing: border-box; }
  html, body {
    width: 1200px; height: 900px; overflow: hidden;
    background: var(--backdrop);
    font-family: "Lato", Arial, sans-serif;
  }
  .canvas { position: relative; width: 1200px; height: 900px; }

  .card {
    position: absolute;
    width: 560px; height: 320px;
    box-shadow: 0 10px 30px rgba(0,0,0,0.45);
  }

  /* Front: blue */
  .card-front {
    left: 40px; top: 120px;
    background: var(--card-blue);
    display: flex; flex-direction: column; align-items: center; justify-content: center;
  }
  .brand { display: flex; align-items: center; gap: 16px; color: var(--ink-dark); }
  .brand-dot {
    width: 58px; height: 58px; border-radius: 50%;
    border: 3px solid var(--ink-dark);
  }
  .brand-name { font-weight: 900; font-size: 56px; letter-spacing: 0.5px; line-height: 1; }
  .tagline {
    margin-top: 34px;
    font-size: 12px; font-weight: 700; letter-spacing: 3.5px;
    color: var(--ink-dark);
  }

  /* Back: white */
  .card-back {
    left: 600px; top: 470px;
    background: var(--card-white);
  }
  .card-back .brand { position: absolute; left: 60px; top: 34px; }
  .card-back .brand-dot { width: 50px; height: 50px; }
  .card-back .brand-name { font-size: 46px; }

  .person { position: absolute; left: 360px; top: 118px; }
  .person-name { font-size: 19px; font-weight: 900; color: var(--accent-blue); letter-spacing: 0.3px; }
  .person-role { font-size: 13px; font-weight: 700; color: var(--ink-black); margin-top: 2px; }

  .service {
    position: absolute; left: 360px; top: 206px;
    font-size: 19px; font-weight: 900; color: var(--accent-blue); letter-spacing: 0.3px;
  }

  .contact { position: absolute; left: 36px; top: 188px; }
  .address { font-size: 15px; font-weight: 900; color: var(--accent-blue); line-height: 1.2; margin-bottom: 12px; }
  .contact-line {
    display: flex; align-items: center; gap: 10px;
    font-size: 15px; font-weight: 700; color: var(--ink-black); margin-bottom: 7px;
  }
  .contact-line svg { width: 16px; height: 14px; fill: var(--icon-teal); }
  .website { font-size: 16px; font-weight: 900; color: var(--ink-black); margin-top: 2px; }
  .website span { color: var(--accent-blue); }
</style>
</head>
<body>
<main class="canvas">

  <section class="card card-front" aria-label="Business card front">
    <div class="brand">
      <span class="brand-dot"></span>
      <span class="brand-name">Innerway</span>
    </div>
    <p class="tagline">YOUR SLOGAN / TAGLINE HERE</p>
  </section>

  <section class="card card-back" aria-label="Business card back">
    <div class="brand">
      <span class="brand-dot"></span>
      <span class="brand-name">Innerway</span>
    </div>

    <div class="person">
      <p class="person-name">MARCUS ELLERY</p>
      <p class="person-role">Managing Director</p>
    </div>

    <p class="service">CONSULTING SERVICES</p>

    <div class="contact">
      <p class="address">Kestrel Bay, Queensland,<br>Australia 4101</p>
      <p class="contact-line">
        <svg viewBox="0 0 16 14" aria-hidden="true">
          <path d="M1 4c0-2 2-3 7-3s7 1 7 3v1h-4V3.5H5V5H1z"/>
          <path d="M4 6h8l2 7H2z"/>
        </svg>
        0400 128 735
      </p>
      <p class="contact-line">
        <svg viewBox="0 0 16 14" aria-hidden="true">
          <path d="M1 2h14v10H1z M2.5 3.5 8 8l5.5-4.5" fill="none" stroke="var(--icon-teal)" stroke-width="1.6"/>
        </svg>
        Info@innerwayco.com
      </p>
      <p class="website">www.<span>innerwayco</span>.com</p>
    </div>
  </section>

</main>
</body>
</html>
```